Corvane Freight Company Business Card Design

We are a company that delivers natural saltwater (from the ocean) to aquarium companies, restaurants and home marine tanks. I would like a new business card to suit.

Must include Name, company name, abn, contact number and website as well as logo (see attached).

Looking for a design that stands out, has a clean but unique appearance.

Double and single sided entries welcome

Business

• Logo

```html
<!DOCTYPE html>
<html lang="en">
<head>
<meta charset="utf-8">
<title>Corvane Freight Company – Business Card</title>
<link rel="stylesheet" href="https://fonts.googleapis.com/css2?family=Source+Sans+3:wght@400;600;700&display=swap">
<style>
  :root {
    --backdrop: #1c1c1c;
    --card-blue: #1a64f0;
    --ink-white: #ffffff;
    --ink-soft: #e6eefc;
    --rule: rgba(255, 255, 255, 0.75);
  }
  * { margin: 0; padding: 0; box-sizing: border-box; }
  html, body {
    width: 1200px;
    height: 412px;
    overflow: hidden;
    background: var(--backdrop);
    font-family: "Source Sans 3", "Helvetica Neue", Arial, sans-serif;
    color: var(--ink-white);
  }
  .canvas {
    position: relative;
    width: 1200px;
    height: 412px;
  }
  .card {
    position: absolute;
    width: 525px;
    height: 300px;
    background: var(--card-blue);
  }
  .card--front { left: 57px; top: 62px; }
  .card--back  { left: 617px; top: 60px; }

  .brand-name {
    position: absolute;
    left: 0;
    width: 100%;
    text-align: center;
    font-weight: 700;
    font-size: 42px;
    letter-spacing: -0.5px;
    color: var(--ink-white);
    line-height: 1;
  }
  .card--front .brand-name { top: 66px; }
  .card--back .brand-name  { top: 118px; }

  .holder {
    position: absolute;
    top: 176px;
    left: 0;
    width: 100%;
    text-align: center;
    font-size: 19px;
    line-height: 1;
  }
  .holder__name { font-weight: 700; }
  .holder__title { font-weight: 400; font-size: 16px; }

  .holder-rule {
    position: absolute;
    top: 209px;
    left: 40px;
    width: 446px;
    height: 2px;
    background: linear-gradient(90deg, rgba(255,255,255,0.2), var(--rule) 20%, var(--rule) 80%, rgba(255,255,255,0.2));
  }

  .address {
    position: absolute;
    top: 230px;
    right: 267px;
    text-align: right;
    font-size: 13px;
    line-height: 19px;
    color: var(--ink-soft);
  }
  .address__company { font-weight: 700; color: var(--ink-white); }

  .contact-divider {
    position: absolute;
    top: 226px;
    left: 273px;
    width: 1px;
    height: 58px;
    background: var(--rule);
  }

  .contacts {
    position: absolute;
    top: 226px;
    left: 284px;
    list-style: none;
    font-size: 13px;
    line-height: 20px;
    color: var(--ink-soft);
  }
  .contacts li { display: flex; align-items: center; gap: 5px; }
  .contacts svg { width: 10px; height: 10px; flex: none; }

  .web-address {
    position: absolute;
    top: 240px;
    left: 0;
    width: 100%;
    text-align: center;
    font-size: 17px;
    letter-spacing: 3px;
    color: var(--ink-soft);
  }
</style>
</head>
<body>
<main class="canvas">
  <section class="card card--front" aria-label="Business card front">
    <p class="brand-name">Corvane Freight</p>
    <p class="holder"><span class="holder__name">Your name,</span> <span class="holder__title">Title</span></p>
    <div class="holder-rule"></div>
    <address class="address">
      <span class="address__company">Corvane Freight Company</span><br>
      Street Name, City Name<br>
      State, City Zip Code
    </address>
    <div class="contact-divider"></div>
    <ul class="contacts">
      <li>
        <svg viewBox="0 0 10 10" aria-hidden="true"><circle cx="5" cy="5" r="4.3" fill="none" stroke="#fff" stroke-width="1"/><path d="M3.3 2.6 l1 1 -0.5 0.6 c0.4 0.8 0.9 1.3 1.6 1.6 l0.6-0.5 1 1 -0.8 0.9 C4.6 7 3 5.4 2.6 3.4z" fill="#fff"/></svg>
        123-456-7890
      </li>
      <li>
        <svg viewBox="0 0 10 10" aria-hidden="true"><circle cx="5" cy="5" r="4.5" fill="#fff"/></svg>
        www.website.com
      </li>
      <li>ABN : 0123456789</li>
    </ul>
  </section>

  <section class="card card--back" aria-label="Business card back">
    <p class="brand-name">Corvane Freight</p>
    <p class="web-address">www.website.com</p>
  </section>
</main>
</body>
</html>
```